Independent theatre company and venue needs funky web design

Web design for theatre company based in Brisbane Australia. Innovative, grassroots theatre space needs to promote shows in quirky industrial venue. Design needs to be funky, arty but website feels solid and business savvy as well. We need a portal for selling tickets online.
Kettle and Drum is the production company behind this project. We also create theatre in fresh, intimate and humanistic ways.
Target Market(s)
ages 20s-80s
Interested in the arts and fresh, quirky local experiences
Industry/Entity Type
It Company
Coding
Coded - Design and coding required
Number of Pages Required
4 page
Requirements
Must have
- Pages:
- Performances (What's on)
- Hire the Venue (info and enquiry form)
- About Kettle and Drum (history and profile)
- Buy Tickets (patrons can purchase tickets to the shows on at the venue)
- Contact Us/Subscribe
Nice to have
- http://www.tinmill77stage.com/
- Similar in content to this one
- Ideally a website I can update shows (so wordpress or similar user friendly)

```html
<!DOCTYPE html>
<html lang="en">
<head>
<meta charset="utf-8">
<title>Kettle and Drum</title>
<link rel="stylesheet" href="https://fonts.googleapis.com/css2?family=Open+Sans:wght@400;600;700&display=swap">
<style>
:root{
  --ink:#1e1e1e;
  --text:#333;
  --muted:#8a8a8a;
  --line:#e6e6e6;
  --dark:#232323;
  --panel:#111;
  --caption:rgba(45,45,45,.88);
  --white:#fff;
  --go:#4a4a4a;
  --fb:#3b5998;--tw:#1da1f2;--gp:#dd4b39;
}
*{box-sizing:border-box;margin:0;padding:0}
html,body{width:884px;height:1200px;overflow:hidden}
body{font-family:"Open Sans",sans-serif;color:var(--text);background:var(--white);position:relative}
.abs{position:absolute}
.site-header{position:absolute;left:0;top:0;width:884px;height:64px;border-bottom:1px solid #eee;box-shadow:0 1px 3px rgba(0,0,0,.05)}
.brand{position:absolute;left:70px;top:18px;display:flex;align-items:center;gap:6px;font-weight:700;font-size:17px;color:var(--ink)}
.brand-dot{width:12px;height:12px;border-radius:50%;background:var(--ink)}
.main-nav{position:absolute;right:73px;top:25px;display:flex;gap:22px;font-size:9px;color:#444}
.main-nav a{color:inherit;text-decoration:none;position:relative}
.main-nav .active{font-weight:600;color:var(--ink)}
.main-nav .active::after{content:"";position:absolute;left:-6px;right:-6px;top:18px;height:3px;background:var(--ink)}
.hero{left:74px;top:86px;width:736px;height:334px;border:2px solid #ddd;background:linear-gradient(100deg,#0d0d0d 0%,#2a2a2a 35%,#4c8fc9 62%,#0b0b0b 100%);box-shadow:0 12px 10px -8px rgba(0,0,0,.35)}
.hero-art{position:absolute;inset:0}
.hero-arrow{position:absolute;top:160px;width:20px;height:30px}
.hero-caption{position:absolute;right:0;top:228px;width:374px;height:69px;background:var(--caption);color:var(--white);font-size:16px;line-height:21px;text-align:right;padding:13px 22px 0 20px}
.event{top:461px;width:174px;height:181px;box-shadow:0 8px 8px -6px rgba(0,0,0,.35)}
.event-img{height:137px}
.event-cap{height:44px;background:var(--panel);color:var(--white);padding:7px 11px 0}
.event-date{font-size:8.5px;color:#ccc}
.event-title{font-size:11.8px;margin-top:1px}
.profile-title{left:71px;top:689px;font-size:19px;font-weight:600;color:var(--ink);letter-spacing:.3px}
.profile-art{left:74px;top:742px;width:144px;height:166px;background:linear-gradient(160deg,#fff 0%,#f3d2b8 40%,#e9c0a0 70%,#fff 100%)}
.profile-text{left:248px;top:738px;width:344px;font-size:9.1px;line-height:15.2px;text-align:justify;color:#333}
.btn-dark{left:250px;top:879px;width:92px;height:26px;background:var(--panel);color:var(--white);font-size:9px;display:flex;align-items:center;justify-content:center}
.book{left:618px;top:695px;width:193px;height:209px;background:var(--panel);color:var(--white);text-align:center}
.book h2{font-size:19px;font-weight:600;margin-top:14px;letter-spacing:.3px}
.book p{font-size:9px;line-height:13.5px;color:#ccc;margin:7px 12px 0}
.book-field{position:absolute;left:13px;width:167px;height:27px;background:var(--white);color:#555;font-size:9px;text-align:left;padding:7px 10px}
.book-go{position:absolute;left:13px;top:163px;width:167px;height:31px;background:var(--go);font-size:16px;display:flex;align-items:center;justify-content:center}
.site-footer{left:0;top:974px;width:884px;height:226px;background:var(--dark);color:#ddd}
.foot-nav{position:absolute;top:38px;left:0;width:884px;text-align:center;font-size:8.5px}
.foot-nav span{margin:0 7px;color:#aaa}
.rule{position:absolute;left:73px;width:740px;height:1px;background:#3a3a3a}
.foot-h{position:absolute;top:106px;font-size:10.5px;color:#ddd}
.social{position:absolute;top:127px;width:24px;height:24px}
.news-input{position:absolute;left:342px;top:127px;width:124px;height:25px;background:#444;color:#888;font-size:8px;padding:7px 11px}
.news-btn{position:absolute;left:466px;top:127px;width:76px;height:25px;background:#111;color:var(--white);font-size:10px;display:flex;align-items:center;justify-content:center}
.contact{position:absolute;right:71px;top:126px;text-align:right;font-size:8.8px;line-height:11px;color:#999}
.copyright{position:absolute;top:195px;width:884px;text-align:center;font-size:8.3px;color:#777}
</style>
</head>
<body>
<header class="site-header">
  <div class="brand"><span class="brand-dot"></span>Kettle and Drum</div>
  <nav class="main-nav">
    <a class="active">Home</a><a>Performances</a><a>Hire the Venue</a><a>About Kettle and Drum</a><a>Buy tickets</a><a>Contact us</a>
  </nav>
</header>

<section class="hero abs">
  <div class="hero-art" role="img" aria-label="Vintage film projector with reels lit by a blue beam"></div>
  <svg class="hero-arrow" style="left:28px" viewBox="0 0 20 30"><polyline points="15,3 4,15 15,27" fill="none" stroke="#bbb" stroke-width="2"/></svg>
  <svg class="hero-arrow" style="right:14px" viewBox="0 0 20 30"><polyline points="5,3 16,15 5,27" fill="none" stroke="#bbb" stroke-width="2"/></svg>
  <div class="hero-caption">In quis consectetur ante. Cras nec porttitor dui. Curabitur vulputate</div>
</section>

<article class="event abs" style="left:73px">
  <div class="event-img" role="img" aria-label="Three mime performers in costume" style="background:linear-gradient(180deg,#3a3a3a,#b83a3a 70%,#c9a36a)"></div>
  <div class="event-cap"><div class="event-date">12-08-2015 &nbsp;|&nbsp; Friday</div><div class="event-title">In quis consectetur ante.</div></div>
</article>
<article class="event abs" style="left:258px">
  <div class="event-img" role="img" aria-label="Child holding a film clapperboard before a red curtain" style="background:linear-gradient(180deg,#d9542a,#e8a25a 60%,#2a2a2a)"></div>
  <div class="event-cap"><div class="event-date">12-08-2015 &nbsp;|&nbsp; Friday</div><div class="event-title">In quis consectetur ante.</div></div>
</article>
<article class="event abs" style="left:445px">
  <div class="event-img" role="img" aria-label="Three children on a stage with painted sky backdrop" style="background:linear-gradient(180deg,#8fb0cc,#dde3e6 55%,#c9a88c)"></div>
  <div class="event-cap"><div class="event-date">12-08-2015 &nbsp;|&nbsp; Friday</div><div class="event-title">In quis consectetur ante.</div></div>
</article>
<article class="event abs" style="left:630px">
  <div class="event-img" role="img" aria-label="Audience members with popcorn in a cinema" style="background:linear-gradient(180deg,#2a3a5a,#7a6a7a 55%,#c23a3a)"></div>
  <div class="event-cap"><div class="event-date">12-08-2015 &nbsp;|&nbsp; Friday</div><div class="event-title">In quis consectetur ante.</div></div>
</article>

<h1 class="profile-title abs">OUR PROFILE</h1>
<div class="profile-art abs" role="img" aria-label="Hand-drawn portrait illustration"></div>
<p class="profile-text abs">Curabitur ex quam, eleifend vel vestibulum sit amet, commodo eget turpis. Integer venenatis erat elit, nec hendrerit tortor feugiat sit amet. Nam bibendum porta orci, sit amet accumsan velit faucibus vel. Vivamus posuere mauris vitae eros venenatis, quis cursus neque aliquet. Cras porttitor arcu ac ipsum ultrices hendrerit. Suspendisse odio purus, eleifend sit amet lacus tincidunt, posuere convallis ex. Ut bibendum arcu vel urna interdum tincidunt. Suspendisse maximus semper nisl, id tristique lectus aliquam id. Fusce egestas, massa non congue vehicula, urna nibh porttitor magna, et vulputate sem metus in velit.</p>
<div class="btn-dark abs">READ MORE</div>

<aside class="book abs">
  <h2>BOOK NOW</h2>
  <p>Lorem ipsum dolor sit amet, consectetur adipiscing elit.</p>
  <div class="book-field" style="top:79px">Name</div>
  <div class="book-field" style="top:118px">Email</div>
  <div class="book-go">GO</div>
</aside>

<footer class="site-footer abs">
  <nav class="foot-nav">Home<span>|</span>Performances<span>|</span>Hire the Venue<span>|</span>About Kettle and Drum<span>|</span>Buy tickets<span>|</span>Contact us</nav>
  <div class="rule" style="top:81px"></div>
  <div class="foot-h" style="left:74px">Follow Us</div>
  <div class="social" style="left:74px;background:var(--fb)" role="img" aria-label="Social link"></div>
  <div class="social" style="left:104px;background:var(--tw)" role="img" aria-label="Social link"></div>
  <div class="social" style="left:135px;background:var(--gp)" role="img" aria-label="Social link"></div>
  <div class="foot-h" style="left:0;width:884px;text-align:center">News letter</div>
  <div class="news-input">Enter your email</div>
  <div class="news-btn">Subscribe</div>
  <div class="foot-h" style="right:71px">Contact Us</div>
  <div class="contact" style="top:126px"><br>Address<br>New Street<br>ph :xxxxx-xxx-xxx</div>
  <div class="rule" style="top:179px"></div>
  <div class="copyright">Northlane Studio © 2015 Allright Reserved</div>
</footer>
</body>
</html>
```